Create an awesome website for a medical clinic

This is a new website for a doctor's office. The site should be clean and modern, easy to navigate.

This is a wellness clinic, we want to help our clients have a healthy, active lifestyle. It should be friendly and inviting, and easy for them to call or schedule an appointment.

The site should be responsive and designed using the attached Bootstrap 3 PSD.

We will provide stock photos, until then please use stock photos from:

pixelharbor.com or
framequarry.com (preferred)

Some example sites of clean and modern designs that we like:

https://tulsaspinecare.com/
http://reachpastjoints.com/
http://turninghealthier.com/

Also attached is a temporary logo you can use.

Reason: Thank you everyone for your great designs - we need a little more time so I'm extending the project.

Need extra days to review

Also, the colors in the new logo I just linked to are the final colors of the logo, so feel free to use any complimentary colors to it.

Hi everyone, The boss wants to change the layout of the site a little bit - here's the revised layout: https://www.filecrate.com/s/k9rt31vx2qp84zn/notes%2011_29_2017.pdf?dl=0 And the graphic assets you can use are here: https://www.filecrate.com/s/k9rt31vx2qp84zn/notes%2011_29_2017.pdf?dl=0 Feel free to change the background color of the "topbar", and change the icons of the "why people trust us" if you want, these are just temporary placeholders. Thanks for your patience and hard work!

Target Market(s)

People seeking medical treatment (wellness clinic)

Industry/Entity Type

Doctor

Number of Pages Required

1 page

Font styles to use
Sans Serif

Colors
0592cd
33a6d7
abd037
9bcb3c

Requirements
Must have
• The home page should have: a strong hero image/slideshow, clinic phone number should be prominent and at the top of the page (in the nav), a "what to expect" section (this is like a FAQs section - see attachment), and a strong call to action (a button to call or schedule an appointment).
• The what to expect section is useful so that prospective clients can determine if we're a good fit for them or not. It's a basic, first-step pre-qualification block of information.
• Social media icons which links to our social media profiles should be included.
Nice to have
• - Link to 3 most recent blog entries
• - Testimonials
• - How a multilevel nav menu looks.

```html
<!DOCTYPE html>
<html lang="en">
<head>
<meta charset="utf-8">
<title>Meadow Wellness Clinic – Blog, Testimonials &amp; Footer</title>
<link rel="stylesheet" href="https://fonts.googleapis.com/css2?family=Open+Sans:ital,wght@0,400;0,600;0,700;1,400;1,600&display=swap">
<style>
  :root{
    --blue:#0592cd;
    --blue-light:#33a6d7;
    --green:#abd037;
    --green-dark:#9bcb3c;
    --footer:#252628;
    --footer-bar:#1b1c1e;
    --white:#ffffff;
    --muted:#d9d9d9;
  }
  *{box-sizing:border-box;margin:0;padding:0}
  html,body{width:1200px;height:1200px;overflow:hidden;background:#fff;font-family:"Open Sans",sans-serif}
  .canvas{position:relative;width:1200px;height:1200px}

  .section-title{position:absolute;left:0;width:1200px;text-align:center;font-weight:600;font-size:30px}
  .blog-title{top:26px;color:var(--blue)}
  .title-rule{position:absolute;left:286px;width:628px;height:3px}
  .blog-rule{top:71px;background:var(--blue)}

  .post-card{position:absolute;top:104px;width:290px;height:288px;background:var(--blue)}
  .post-photo{height:156px}
  .post-icon{position:absolute;left:125px;top:138px;width:40px;height:40px;border-radius:50%;background:var(--blue);border:3px solid var(--white);display:flex;align-items:center;justify-content:center}
  .post-headline{position:absolute;top:180px;width:100%;text-align:center;color:var(--white);font-weight:600;font-size:20px}
  .post-excerpt{position:absolute;left:14px;right:12px;top:207px;color:var(--white);font-size:14.6px;line-height:17.5px}
  .read-more{position:absolute;right:-4px;top:262px;height:21px;padding:0 10px 0 14px;background:var(--green-dark);color:var(--white);font-weight:600;font-size:14.5px;line-height:21px;clip-path:polygon(8px 0,100% 0,100% 100%,0 100%)}
  .slider-arrow{position:absolute;top:228px;width:33px;height:40px;background:var(--blue);display:flex;align-items:center;justify-content:center}
  .arrow-prev{left:95px;border-radius:5px 0 0 5px}
  .arrow-next{left:1072px;border-radius:0 5px 5px 0}

  .testimonials{position:absolute;left:140px;top:428px;width:920px;height:356px;background:linear-gradient(180deg,#6b6577 0%,#877a83 28%,#5f6476 55%,#474b5c 100%)}
  .testimonials-title{top:18px;color:#e8e8ea;font-weight:400;font-size:29px;width:920px}
  .testimonials-rule{top:61px;left:146px;background:#dedede}
  .quote-box{position:absolute;left:146px;top:72px;width:628px;height:260px;background:rgba(90,90,100,.45)}
  .quote-text{position:absolute;left:76px;top:20px;white-space:nowrap;color:#eeeeee;font-style:italic;font-size:14.6px;line-height:17.4px}
  .quote-author{position:absolute;right:92px;top:200px;color:#eeeeee;font-style:italic;font-weight:600;font-size:16px}
  .quote-mark{position:absolute}
  .quote-arrow{position:absolute;top:184px;width:32px;height:38px;background:rgba(70,70,80,.55);display:flex;align-items:center;justify-content:center}

  .site-footer{position:absolute;left:75px;top:820px;width:1050px;height:355px;background:var(--footer)}
  .footer-divider{position:absolute;top:33px;width:1px;height:246px;background:#444}
  .footer-col{position:absolute;top:57px}
  .footer-heading{color:var(--green);font-weight:600;font-size:19px;margin-bottom:22px}
  .footer-list{list-style:none;margin-top:-10px}
  .footer-list li{display:flex;align-items:center;gap:12px;color:#e5e5e5;font-size:15px;height:35.5px}
  .contact-row{display:flex;gap:10px;color:#e5e5e5;font-size:15px;line-height:17px}
  .follow-text{color:#e5e5e5;font-size:15px;line-height:17px;width:240px}
  .social-row{display:flex;gap:14px;margin-top:36px}
  .social-link{display:flex;align-items:center;gap:5px;color:var(--green);font-size:13px;font-weight:600}
  .social-dot{width:10px;height:10px;border-radius:50%;border:2px solid var(--green)}
  .footer-bar{position:absolute;left:0;bottom:0;width:100%;height:36px;background:var(--footer-bar);color:#dddddd;font-size:13.5px;text-align:center;line-height:36px}
</style>
</head>
<body>
<main class="canvas">

  <h2 class="section-title blog-title">Blog Posts</h2>
  <div class="title-rule blog-rule"></div>

  <div class="slider-arrow arrow-prev"><svg width="16" height="30" viewBox="0 0 16 30"><path d="M14 2 2 15l12 13" fill="none" stroke="#fff" stroke-width="2"/></svg></div>
  <div class="slider-arrow arrow-next"><svg width="16" height="30" viewBox="0 0 16 30"><path d="M2 2l12 13L2 28" fill="none" stroke="#fff" stroke-width="2"/></svg></div>

  <article class="post-card" style="left:140px">
    <div class="post-photo" role="img" aria-label="Photo of women meditating on yoga mats in a bright studio" style="background:linear-gradient(180deg,#e9e4dc 0%,#d8b58a 55%,#3d7fc4 100%)"></div>
    <div class="post-icon"><svg width="18" height="20" viewBox="0 0 18 20"><rect x="4" y="1" width="12" height="15" rx="1" fill="none" stroke="#fff" stroke-width="1.5"/><rect x="1" y="4" width="12" height="15" rx="1" fill="var(--blue)" stroke="#fff" stroke-width="1.5"/><path d="M4 9h6M4 12h6M4 15h6" stroke="#fff" stroke-width="1.3"/></svg></div>
    <h3 class="post-headline">Headline Example 1</h3>
    <p class="post-excerpt">Lorem ipsum dolor sit amet, mus non convallis turpis a, sed sollicitudin quisquam wisi lectus proin ...</p>
    <span class="read-more">Read more</span>
  </article>

  <article class="post-card" style="left:455px">
    <div class="post-photo" role="img" aria-label="Photo of a doctor talking with an older patient" style="background:linear-gradient(180deg,#ecebe8 0%,#d7d2ca 60%,#a8b3c4 100%)"></div>
    <div class="post-icon"><svg width="18" height="20" viewBox="0 0 18 20"><rect x="4" y="1" width="12" height="15" rx="1" fill="none" stroke="#fff" stroke-width="1.5"/><rect x="1" y="4" width="12" height="15" rx="1" fill="var(--blue)" stroke="#fff" stroke-width="1.5"/><path d="M4 9h6M4 12h6M4 15h6" stroke="#fff" stroke-width="1.3"/></svg></div>
    <h3 class="post-headline">Headline Example 2</h3>
    <p class="post-excerpt">Lorem ipsum dolor sit amet, mus non convallis turpis a, sed sollicitudin quisquam wisi lectus proin ...</p>
    <span class="read-more">Read more</span>
  </article>

  <article class="post-card" style="left:770px">
    <div class="post-photo" role="img" aria-label="Photo of a woman training on a gym machine with a coach" style="background:linear-gradient(100deg,#3a3a36 0%,#8a8578 50%,#e8e6d8 100%)"></div>
    <div class="post-icon"><svg width="18" height="20" viewBox="0 0 18 20"><rect x="4" y="1" width="12" height="15" rx="1" fill="none" stroke="#fff" stroke-width="1.5"/><rect x="1" y="4" width="12" height="15" rx="1" fill="var(--blue)" stroke="#fff" stroke-width="1.5"/><path d="M4 9h6M4 12h6M4 15h6" stroke="#fff" stroke-width="1.3"/></svg></div>
    <h3 class="post-headline">Headline Example 3</h3>
    <p class="post-excerpt">Lorem ipsum dolor sit amet, mus non convallis turpis a, sed sollicitudin quisquam wisi lectus proin ...</p>
    <span class="read-more">Read more</span>
  </article>

  <section class="testimonials" role="img" aria-label="Background photo of a person meditating on a beach at dusk">
    <h2 class="section-title testimonials-title">Testimonials</h2>
    <div class="title-rule testimonials-rule"></div>
    <div class="quote-arrow" style="left:101px"><svg width="14" height="26" viewBox="0 0 14 26"><path d="M12 2 2 13l10 11" fill="none" stroke="#fff" stroke-width="1.6"/></svg></div>
    <div class="quote-arrow" style="left:787px"><svg width="14" height="26" viewBox="0 0 14 26"><path d="M2 2l10 11L2 24" fill="none" stroke="#fff" stroke-width="1.6"/></svg></div>
    <div class="quote-box">
      <svg class="quote-mark" style="left:11px;top:22px" width="54" height="42" viewBox="0 0 54 42"><path d="M4 42V22C4 10 10 3 22 0v8c-6 2-9 6-9 12h9v22zM32 42V22c0-12 6-19 18-22v8c-6 2-9 6-9 12h9v22z" fill="#e6e6e6"/></svg>
      <p class="quote-text">Lorem Ipsum is simply dummy text of the printing and typesetting<br>industry. Lorem Ipsum has been the industry's standard dummy text ever since the<br>1500s, when an unknown printer took a galley of type and scrambled it to make a<br>type specimen book. It has survived not only five centuries, but also the leap into<br>electronic typesetting, remaining<br>essentially unchanged. It was popularised in the 1960s with the release of Letterfold<br>sheets containing Lorem Ipsum passages, and more recently with desktop publishing<br>software like Quill LayoutDesk including versions of Lorem Ipsum.</p>
      <span class="quote-author">Daniel Harper</span>
      <svg class="quote-mark" style="left:562px;top:206px" width="54" height="42" viewBox="0 0 54 42"><path d="M4 0v20c0 12 6 19 18 22v-8c-6-2-9-6-9-12h9V0zM32 0v20c0 12 6 19 18 22v-8c-6-2-9-6-9-12h9V0z" fill="#e6e6e6" transform="rotate(180 27 21)"/></svg>
    </div>
  </section>

  <footer class="site-footer">
    <div class="footer-divider" style="left:367px"></div>
    <div class="footer-divider" style="left:682px"></div>

    <div class="footer-col" style="left:97px">
      <h4 class="footer-heading">Recent Posts</h4>
      <ul class="footer-list">
        <li><svg width="20" height="20" viewBox="0 0 20 20"><circle cx="10" cy="10" r="8.5" fill="none" stroke="var(--green)" stroke-width="1.6"/><path d="M8 6l4 4-4 4" fill="none" stroke="var(--green)" stroke-width="1.8"/></svg>Sonsectetur Sedipiscing Elit</li>
        <li><svg width="20" height="20" viewBox="0 0 20 20"><circle cx="10" cy="10" r="8.5" fill="none" stroke="var(--green)" stroke-width="1.6"/><path d="M8 6l4 4-4 4" fill="none" stroke="var(--green)" stroke-width="1.8"/></svg>Fed do Eiusmod Tempor</li>
        <li><svg width="20" height="20" viewBox="0 0 20 20"><circle cx="10" cy="10" r="8.5" fill="none" stroke="var(--green)" stroke-width="1.6"/><path d="M8 6l4 4-4 4" fill="none" stroke="var(--green)" stroke-width="1.8"/></svg>Incididunt ut Labore et Dolore</li>
        <li><svg width="20" height="20" viewBox="0 0 20 20"><circle cx="10" cy="10" r="8.5" fill="none" stroke="var(--green)" stroke-width="1.6"/><path d="M8 6l4 4-4 4" fill="none" stroke="var(--green)" stroke-width="1.8"/></svg>Nostrud Exercitation Ullamco</li>
        <li><svg width="20" height="20" viewBox="0 0 20 20"><circle cx="10" cy="10" r="8.5" fill="none" stroke="var(--green)" stroke-width="1.6"/><path d="M8 6l4 4-4 4" fill="none" stroke="var(--green)" stroke-width="1.8"/></svg>Magna Aliqua</li>
      </ul>
    </div>

    <div class="footer-col" style="left:412px">
      <h4 class="footer-heading">Contact</h4>
      <div class="contact-row"><svg width="20" height="18" viewBox="0 0 20 18"><path d="M10 1 1 9h3v8h4v-5h4v5h4V9h3z" fill="var(--green)"/></svg><span>48 Willow Crest Avenue<br>Fairlane, MD 20990</span></div>
      <div class="contact-row" style="margin-top:19px"><svg width="20" height="18" viewBox="0 0 20 18"><path d="M2 6c0-3 16-3 16 0v2h-4V6H6v2H2zM5 9h10l3 8H2z" fill="var(--green)"/><circle cx="10" cy="13" r="2" fill="var(--footer)"/></svg><span>305 - 555 - 0148</span></div>
      <div class="contact-row" style="margin-top:24px"><svg width="20" height="18" viewBox="0 0 20 18"><rect x="1" y="3" width="18" height="12" fill="var(--green)"/><path d="M1 3l9 7 9-7" fill="none" stroke="var(--footer)" stroke-width="1.5"/></svg><span>hello@meadowclinic.com</span></div>
    </div>

    <div class="footer-col" style="left:725px">
      <h4 class="footer-heading">Follow Us</h4>
      <p class="follow-text">Lorem ipsum dolor sit amet, consectetur adipiscing elit, sed do eiusmod tempor incididunt ut labore et dolore magna aliqua.</p>
      <div class="social-row">
        <span class="social-link"><span class="social-dot"></span>Kite</span>
        <span class="social-link"><span class="social-dot"></span>Pulse</span>
        <span class="social-link"><span class="social-dot"></span>Loop</span>
        <span class="social-link"><span class="social-dot"></span>Nest</span>
        <span class="social-link"><span class="social-dot"></span>Orbit</span>
      </div>
    </div>

    <div class="footer-bar">Copyrght 2017 - Meadow Wellness Clinic</div>
  </footer>

</main>
</body>
</html>
```